Resposive web site in 4 languages + image gallery + logo design

We need a web page, which will work on all devices.
I have uploaded web page concept.
Company name: Praxelun
Industry/Entity Type
It Company
Logo Text
quality matters
Coding
Coded - Design and coding required
Number of Pages Required
1 page

```html
<!DOCTYPE html>
<html lang="en">
<head>
<meta charset="utf-8">
<title>Praxelun</title>
<link href="https://fonts.googleapis.com/css2?family=Cinzel:wght@400;700&family=Lato:wght@400;700&display=swap" rel="stylesheet">
<style>
:root{
  --orange:#f7941d;
  --navy:#1d4e7e;
  --navy-deep:#17426b;
  --ink:#1b1b1b;
  --text:#3a3a3a;
  --grey-bg:#f0f0f0;
  --line:#d8d8d8;
  --white:#ffffff;
}
*{box-sizing:border-box;margin:0;padding:0}
html,body{width:1200px;height:2535px;overflow:hidden}
body{font-family:"Lato",sans-serif;color:var(--text);background:var(--white);position:relative}
.abs{position:absolute}
section,header,footer{position:relative;width:1200px}

.topbar{height:37px;background:var(--orange)}
.topbar .social,.topbar .lang{position:absolute;top:0;height:37px;background:var(--navy);color:var(--white);font-weight:700;font-size:16px;display:flex;align-items:center;justify-content:center;gap:8px}
.topbar .social{left:857px;width:145px}
.topbar .lang{left:1006px;width:133px}
.social .sq{width:22px;height:22px;background:var(--white);border-radius:3px}
.lang .dot{width:16px;height:16px;border-radius:50%;background:var(--white)}
.lang .caret{width:0;height:0;border-left:6px solid transparent;border-right:6px solid transparent;border-top:7px solid var(--white)}

.masthead{height:78px;background:var(--white)}
.brand{left:61px;top:18px;font-family:"Cinzel",serif;font-weight:700;font-size:34px;color:var(--orange);letter-spacing:1px}
.nav{right:61px;top:26px;display:flex;gap:58px;list-style:none;font-family:"Cinzel",serif;font-size:17px;color:var(--ink)}
.nav .active{color:var(--orange);border-bottom:2px solid var(--orange);padding-bottom:4px}

.hero{height:488px;background:linear-gradient(180deg,#1f3f86 0%,#2c5aa8 35%,#6b7d93 62%,#4a6a7c 78%,#2e4a3a 100%)}
.hero-photo{inset:0}
.hero-title{left:61px;top:322px;font-family:"Cinzel",serif;font-size:36px;line-height:46px;color:var(--white);letter-spacing:1px}
.quote-btn{left:61px;top:434px;width:210px;height:42px;background:var(--orange);border-radius:21px;color:var(--white);font-weight:700;font-size:20px;display:flex;align-items:center;padding-left:57px}
.quote-btn .ico{position:absolute;left:2px;top:2px;width:38px;height:38px;border-radius:50%;background:var(--white);border:3px solid var(--navy)}
.dots{left:61px;top:571px;display:flex;gap:9px}
.dots span{width:14px;height:14px;border-radius:50%;background:#d5d5d5}
.dots .on{background:var(--navy);border:2px solid #d5d5d5}

.heading{font-family:"Cinzel",serif;font-weight:700;font-size:34px;text-align:center;color:var(--ink);letter-spacing:1px}
.heading em{font-style:normal;font-weight:400;color:var(--orange)}
.rule{left:333px;width:534px;height:1px;background:var(--line)}
.rule::after{content:"";position:absolute;left:201px;top:-1px;width:132px;height:2px;background:var(--navy)}

.welcome{height:284px}
.welcome .heading{position:absolute;top:36px;width:100%}
.welcome .rule{top:83px}
.welcome p{position:absolute;left:60px;width:1080px;top:104px;text-align:center;font-size:14px;line-height:23px}
.btn{background:var(--navy);color:var(--white);font-size:13px;display:flex;align-items:center;justify-content:center;border-radius:3px}
.read-more{left:546px;top:208px;width:106px;height:32px}

.services-head{height:431px;background:var(--grey-bg)}
.services-head .heading{position:absolute;top:36px;width:100%}
.services-head .rule{top:85px}
.service-row{height:338px;background:var(--white)}
.service-row.alt{height:335px;background:var(--grey-bg)}
.photo{border:1px solid #ccc}
.thumbs{display:flex;flex-direction:column;gap:6px}
.thumbs span{width:54px;height:52px;border:2px solid #ddd;display:block}
.thumbs .sel{border-color:var(--orange)}
.svc-title{font-size:25px;color:var(--navy);font-weight:400}
.svc-text{font-size:15px;line-height:31.5px;color:var(--text)}

.band{height:243px;background:linear-gradient(180deg,#1e4a78,#163d66);color:var(--white);text-align:center}
.band p{position:absolute;top:52px;width:100%;font-size:18px;line-height:30px}
.band .band-rule{left:400px;top:157px;width:400px;height:1px;background:rgba(255,255,255,.3)}
.band .tagline{position:absolute;top:178px;width:100%;color:var(--orange);font-weight:700;font-size:18px}

.site-footer{height:254px;background:var(--white)}
.col-title{font-family:"Cinzel",serif;font-size:19px;color:var(--ink);letter-spacing:1px;padding-bottom:8px;border-bottom:1px solid var(--line)}
.links{list-style:none;font-size:14px;color:var(--ink)}
.links li{height:39px}
.links li::before{content:"›";margin-right:8px;color:#777}
.links .cur{color:var(--orange);font-weight:700}
.contact-item{font-size:14px;line-height:19px;color:var(--text);padding-left:33px;position:relative}
.contact-item svg{position:absolute;left:2px;top:1px}
.field{border:1px dashed #c8c8c8;font-size:13px;color:#444;padding:7px 10px;background:var(--white)}
.submit{background:var(--orange);border-radius:2px;font-weight:700}
.copyright{height:47px;background:var(--navy);color:var(--white);font-size:13px;display:flex;align-items:center;justify-content:center;letter-spacing:.5px}
</style>
</head>
<body>

<header class="topbar">
  <div class="social">Find Us On <span class="sq"></span></div>
  <div class="lang"><span class="dot"></span>English <span class="caret"></span></div>
</header>

<header class="masthead">
  <div class="abs brand">PRAXELUN</div>
  <ul class="abs nav">
    <li class="active">Home</li>
    <li>Services</li>
    <li>About Us</li>
    <li>Contact Us</li>
  </ul>
</header>

<section class="hero">
  <div class="abs hero-photo" role="img" aria-label="Modern stone and timber house with pool at dusk"></div>
  <h1 class="abs hero-title" style="font-weight:400">ARE YOU INTERESTED<br>IN AN ESTIMATE?</h1>
  <div class="abs quote-btn"><span class="ico"></span>GET A QUOTE</div>
  <div class="abs dots"><span></span><span class="on"></span><span></span></div>
</section>

<section class="welcome">
  <h2 class="heading">WELCOME TO <em>PRAXELUN</em></h2>
  <div class="abs rule"></div>
  <p>Praxelun is a company whose business operations include making wooden products, restoration and building structures from natural stone. All of our products are made by craftsmen and specialists who have extensive experience and knowledge in their fields. The products we offer are always handmade and we take the requests and ideas of the specific client into account We always strive to achieve the best possible quality.</p>
  <div class="abs btn read-more">READ MORE</div>
</section>

<section class="services-head">
  <h2 class="heading">OUR <em>SERVICES</em></h2>
  <div class="abs rule"></div>
  <div class="abs photo" style="left:61px;top:141px;width:287px;height:235px;background:linear-gradient(135deg,#6b5a48,#b59a78 55%,#3a302a)" role="img" aria-label="Solid wood dining table with dark leather chairs"></div>
  <div class="abs thumbs" style="left:362px;top:145px">
    <span style="background:#8a6a4a"></span><span style="background:#4a3a2e"></span><span style="background:#7a5238"></span><span style="background:#c89a6a"></span>
  </div>
  <h3 class="abs svc-title" style="left:463px;top:134px">WOOD WORKS</h3>
  <p class="abs svc-text" style="left:463px;top:180px;width:680px">Timber is, in essence, a natural and warm material. Wood is also relatively durable and easy to work with, which has made it a favourite of builders throughout history. Our goal is to offer suitable products and quality furniture with installation and after-sales service to all of our clients. In order to achieve this, we’ ready to help our clients in all stages of construction from design to production and maintenance</p>
</section>

<section class="service-row">
  <h3 class="abs svc-title" style="left:61px;top:50px">STONE WORKS</h3>
  <p class="abs svc-text" style="left:61px;top:96px;width:700px">The natural stone found in the ground has been used in construction for centuries because of its durability. A structure built by a skilled craftsman from natural stone is unique, genuine and durable, and perfect for our bracing climate. Our experienced craftsmen are ready to help you in all stages of construction from planning to completion.</p>
  <div class="abs photo" style="left:781px;top:56px;width:287px;height:235px;background:linear-gradient(160deg,#8a8a86,#a9a497 50%,#4f6a3e)" role="img" aria-label="Natural stone house wall and garden planter"></div>
  <div class="abs thumbs" style="left:1083px;top:60px">
    <span style="background:#9a9890"></span><span class="sel" style="background:#7f8a6a"></span><span style="background:#6a7058"></span><span style="background:#3e3a34"></span>
  </div>
</section>

<section class="service-row alt">
  <div class="abs photo" style="left:61px;top:53px;width:287px;height:233px;background:linear-gradient(135deg,#8a7e6e,#c8bca8 50%,#6a5a48)" role="img" aria-label="Restored rustic dining room with chandeliers and clock"></div>
  <div class="abs thumbs" style="left:362px;top:57px">
    <span style="background:#a08052"></span><span class="sel" style="background:#7a5a40"></span><span style="background:#8a8a8a"></span><span style="background:#c08a3a"></span>
  </div>
  <h3 class="abs svc-title" style="left:463px;top:58px">RESTORATION</h3>
  <p class="abs svc-text" style="left:463px;top:104px;width:680px">It’s good to see that fixing old things has become popular again in recent years and people are trying to find ways to preserve valuable old windows and pieces of furniture before deciding to replace them. It is possible to give a new life to almost any wooden door,window, piece of furniture or staircase. The extensive experience of our craftsmen will help you achieve the desired result.</p>
</section>

<section class="band">
  <p>All of our products are made by craftsmen and specialists who have extensive experience and knowledge in their fields.<br>The products we offer are always handmade and we take the requests and ideas of the specific client into account<br>We always strive to achieve the best possible quality.</p>
  <div class="abs band-rule"></div>
  <div class="tagline">QUALITY MATTERS, PRAXELUN</div>
</section>

<footer class="site-footer">
  <div class="abs" style="left:61px;top:37px;width:148px">
    <h4 class="col-title" style="font-weight:400">QUICK LINKS</h4>
    <ul class="links" style="margin-top:16px">
      <li class="cur">Home</li><li>Services</li><li>About Us</li><li>Contact Us</li>
    </ul>
  </div>
  <div class="abs" style="left:286px;top:37px;width:252px">
    <h4 class="col-title" style="font-weight:400">CONTACT DETAILS</h4>
    <div class="contact-item" style="margin-top:16px">
      <svg width="14" height="20" viewBox="0 0 14 20"><path d="M7 0a7 7 0 0 0-7 7c0 5 7 13 7 13s7-8 7-13a7 7 0 0 0-7-7z" fill="#f7941d"/><circle cx="7" cy="7" r="2.6" fill="#fff"/></svg>
      <b style="color:var(--ink)">PRAXELUN</b><br>Lindra 12, 10415 Harvel<br>Estonia
    </div>
    <div class="contact-item" style="margin-top:19px">
      <svg width="16" height="16" viewBox="0 0 16 16"><path d="M3 1l3 3-2 2c1 2 3 4 5 5l2-2 3 3-2 3C6 15 1 10 1 3z" fill="#f7941d"/></svg>
      555-014-2290
    </div>
    <div class="contact-item" style="margin-top:19px">
      <svg width="16" height="12" viewBox="0 0 16 12"><rect width="16" height="12" rx="1" fill="#f7941d"/><path d="M1 1l7 6 7-6" stroke="#fff" stroke-width="1.4" fill="none"/></svg>
      sales@praxelun.com
    </div>
  </div>
  <div class="abs" style="left:610px;top:37px;width:531px">
    <h4 class="col-title" style="font-weight:400">QUICK INQUIRY</h4>
  </div>
  <div class="abs field" style="left:614px;top:92px;width:250px;height:34px">Name</div>
  <div class="abs field" style="left:614px;top:139px;width:250px;height:34px">Phone</div>
  <div class="abs field" style="left:614px;top:188px;width:250px;height:34px">Email</div>
  <div class="abs field" style="left:877px;top:92px;width:262px;height:81px">Message</div>
  <div class="abs btn submit" style="left:877px;top:190px;width:85px;height:32px">SUBMIT</div>
</footer>

<div class="copyright">COPYRIGHT © 2016 PRAXELUN. ALL RIGHTS RESERVED.</div>

</body>
</html>
```